Hard-File Archival Services Billboard (Digitization Service) for Attorneys/Law Firms

I need a billboard design for my company "Velkor Legal Aides" that advertises our primary service: Digitization of closed client files, for law firms and attorneys. Our system works as follows: 1) We get a call about a firm that wants to digitize their archived (closed) client files (which usually find their way to file cabinets or bankers boxes), 2) We go and pick those up from the law firm, 3) We bring them to our digitization facility, scan them in, and convert them into searchable PDF/A files, and 4) We upload them on the cloud, give the client a URL to visit their files whenever they want, and we delete them when requested by the client (usually for the retention duration for Missouri's rules of professional conduct, which is 6 years). It would be really cool to see "Velkor Legal Aides" and the logo clearly on the billboard, some simple sentence relating to "Missouri's best digitizing and cloud storage service for closed client files for attorneys" (or something shorter, you get the point), with maybe a linear set of photos and arrows (as follows 1. A photo of a file cabinet opened with files hanging out of it, 2. an arrow pointing to a person scanning in documents in a big scanner (maybe with a Velkor Legal Aidez logo on it?), 3. An arrow pointing to a "secure" appearing cloud (representing cloud storage), and 4. the client sitting at a computer with an arrow pointing back to the cloud (showing the client is accessing the cloud files through the computer). Our website is www.velkorlegalaides.example if you want to glean any additional information from there. Thanks! Oh yes, I should also say the billboard dimensions (in the event you need this for photo aspect ratio) will be as follows: 14 feet tall by 48 feet wide.
Target Market(s)
Attorneys in Springfield, Missouri
Industry/Entity Type
Legal
Look and feel

```html
<!DOCTYPE html>
<html lang="en">
<head>
<meta charset="utf-8">
<title>Velkor Legal Aides – Digitize &amp; Archive Billboard</title>
<link href="https://fonts.googleapis.com/css2?family=Oswald:wght@500;700&display=swap" rel="stylesheet">
<style>
  :root {
    --page-bg: #e9ecef;
    --board-black: #161616;
    --board-black-light: #262626;
    --brand-orange: #f4a224;
    --brand-orange-deep: #d9841a;
    --ink-black: #141414;
    --paper-white: #f2f2f2;
    --tag-shadow: #9a9a9a;
  }
  html, body {
    margin: 0;
    width: 1200px;
    height: 900px;
    overflow: hidden;
    background: var(--page-bg);
  }
  .billboard {
    position: absolute;
    left: 40px;
    top: 286px;
    width: 1120px;
    height: 328px;
    display: block;
    font-family: "Oswald", "Arial Narrow", sans-serif;
  }
  .headline { font-weight: 700; font-size: 137px; }
  .subline { font-weight: 700; font-size: 58px; fill: var(--paper-white); }
  .tagline-text { font-weight: 700; font-size: 28px; fill: var(--ink-black); }
  .audience-text { font-weight: 700; font-size: 32px; fill: var(--ink-black); }
  .brand-name { font-weight: 700; fill: var(--ink-black); }
  .phone { font-weight: 700; font-size: 46px; fill: var(--ink-black); }
</style>
</head>
<body>
<svg class="billboard" viewBox="0 0 1120 328" role="img" aria-label="Velkor Legal Aides billboard: Digitize and archive closed client files, accessible online">
  <defs>
    <radialGradient id="board-shade" cx="45%" cy="40%" r="70%">
      <stop offset="0" stop-color="var(--board-black-light)"/>
      <stop offset="1" stop-color="var(--board-black)"/>
    </radialGradient>
    <linearGradient id="orange-fill" x1="0" y1="0" x2="0" y2="1">
      <stop offset="0" stop-color="var(--brand-orange-deep)"/>
      <stop offset="0.5" stop-color="var(--brand-orange)"/>
      <stop offset="1" stop-color="var(--brand-orange-deep)"/>
    </linearGradient>
  </defs>

  <!-- board background -->
  <rect class="board-bg" x="0" y="0" width="1120" height="328" fill="url(#board-shade)"/>

  <!-- headline -->
  <text class="headline" x="38" y="154" fill="url(#orange-fill)" textLength="820" lengthAdjust="spacingAndGlyphs">DIGITIZE &amp; ARCHIVE</text>

  <!-- subline -->
  <text class="subline" x="36" y="225" textLength="791" lengthAdjust="spacingAndGlyphs">CLOSED CLIENT FILES, ACCESSIBLE ONLINE</text>

  <!-- tagline strip -->
  <rect class="tagline-strip" x="0" y="255" width="840" height="41" fill="var(--brand-orange-deep)"/>
  <text class="tagline-text" x="38" y="286" textLength="764" lengthAdjust="spacingAndGlyphs">VELKOR LEGAL AIDES - MISSOURI'S BEST DIGITIZING AND CLOUD STORAGE SERVICE</text>

  <!-- orange corner panel -->
  <polygon class="corner-edge" points="960,0 968,0 793,328 785,328" fill="var(--paper-white)"/>
  <polygon class="corner-panel" points="968,0 1120,0 1120,328 793,328" fill="url(#orange-fill)"/>

  <!-- audience tag -->
  <polygon class="audience-tag-fold" points="913,41 895,80 913,80" fill="var(--tag-shadow)"/>
  <rect class="audience-tag" x="913" y="41" width="204" height="42" fill="var(--paper-white)"/>
  <text class="audience-text" x="927" y="75" textLength="176" lengthAdjust="spacingAndGlyphs">FOR ATTORNEYS</text>

  <!-- brand name -->
  <circle class="brand-dot" cx="952" cy="166" r="20" fill="none" stroke="var(--ink-black)" stroke-width="5"/>
  <text class="brand-name" x="982" y="160" font-size="38" textLength="104" lengthAdjust="spacingAndGlyphs">VELKOR</text>
  <text class="brand-name" x="982" y="196" font-size="30" textLength="104" lengthAdjust="spacingAndGlyphs">LEGAL AIDES</text>

  <!-- phone -->
  <text class="phone" x="863" y="296" textLength="226" lengthAdjust="spacingAndGlyphs">(417) 555-0148</text>
</svg>
</body>
</html>
```